Real Estate Brokerage Informational Handbill

A 4 X 6 handbill to promote a real estate brokerage modeled after the design attached including attached logo and information.
These handbills should provide a high-level overview of what we do at the brokerage and should be attractive and be inviting.
The goal of the handbill is to have motivated clients in the market to buy or sell their home or property call or visit our website

Target Market(s)

Buyers and sellers of real estate in the Rochester NY area ages 24 - 60

Industry/Entity Type

Real Estate

Font styles to use
Sans Serif

Requirements
Must have
• Please include all the information contained on current handbill
• remove the line "we will walk you through the home buying process at no cost to you".
• replace with "come to one of our monthly first-time buyer informational sessions".
• add the phrase "have your reviewed and receive customized Home Purchase Plan"
• Add the slogan "Brightwell Keys Helping Motivated People Achieve Their Real Estate Goals"
Nice to have
• 2 sided design

```html
<!DOCTYPE html>
<html lang="en">
<head>
<meta charset="utf-8">
<title>Brightwell Keys Handbill</title>
<link rel="stylesheet" href="https://fonts.googleapis.com/css2?family=PT+Serif:wght@400;700&display=swap">
<style>
  :root {
    --page: #ffffff;
    --slate: #333843;
    --slate-back: #363c47;
    --ink: #2a2e36;
    --white: #ffffff;
    --soft-white: #e4e4e6;
    --accent: #d9728f;
    --photo-light: #d9d9dc;
    --photo-mid: #c9c3c6;
    --photo-pink: #e3a3b4;
  }
  * { box-sizing: border-box; margin: 0; padding: 0; }
  html, body { width: 1200px; height: 900px; overflow: hidden; background: var(--page); }
  body { position: relative; font-family: "PT Serif", Georgia, serif; }

  .side { position: absolute; top: 18px; height: 864px; overflow: hidden; text-align: center; }
  .side--front { left: 17px; width: 576px; }
  .side--back { left: 607px; width: 577px; background: var(--slate-back); color: var(--white); }

  .photo-area {
    position: absolute; inset: 0;
    background: linear-gradient(100deg, var(--photo-light) 0%, var(--photo-mid) 40%, var(--photo-pink) 70%, var(--photo-light) 100%);
  }
  .wave { position: absolute; inset: 0; }

  .brand {
    position: absolute; left: 0; right: 0; top: 138px;
    display: flex; justify-content: center; align-items: center; gap: 12px;
    font-weight: 700; font-size: 34px; letter-spacing: 1px;
  }
  .brand-dot { width: 16px; height: 16px; border-radius: 50%; background: var(--accent); }
  .side--front .brand { left: 200px; right: -10px; color: var(--ink); }
  .side--back .brand { color: var(--white); }

  .slogan {
    position: absolute; left: 200px; right: -10px; top: 254px;
    font-weight: 700; font-size: 18.5px; line-height: 24px; color: var(--ink);
  }
  .specialists {
    position: absolute; left: 200px; right: -10px; top: 332px;
    font-size: 14.5px; line-height: 19.5px; color: var(--ink);
  }
  .sessions {
    position: absolute; left: 0; right: 0; top: 758px;
    font-weight: 700; font-size: 17.5px; line-height: 24px; color: var(--white);
    padding-left: 0; width: 576px; transform: translateX(-8px);
  }

  .services {
    position: absolute; left: 0; right: 0; top: 258px; list-style: none;
    font-weight: 700; font-size: 22.5px; line-height: 29px;
  }
  .sell { position: absolute; left: 0; right: 0; top: 448px; font-weight: 700; }
  .sell-question { font-size: 20px; line-height: 28px; }
  .sell-call { font-size: 45px; line-height: 50px; }
  .sell-free { font-size: 17px; line-height: 22px; }
  .sell-phone { font-size: 52px; line-height: 62px; color: var(--soft-white); letter-spacing: 1px; }
  .contact {
    position: absolute; left: 0; right: 0; top: 763px;
    font-weight: 700; font-size: 17px; line-height: 25px;
  }
</style>
</head>
<body>
  <section class="side side--front">
    <div class="photo-area" role="img" aria-label="Photo of a person in a pink shirt holding out house keys on a ring"></div>
    <svg class="wave" width="576" height="864" viewBox="0 0 576 864" aria-hidden="true">
      <path d="M0,545 C60,655 170,740 300,728 C420,716 495,640 576,612 L576,864 L0,864 Z" fill="var(--slate)"/>
      <path d="M0,530 C60,645 170,728 300,716 C420,704 495,628 576,600" fill="none" stroke="#ffffff" stroke-opacity="0.85" stroke-width="2"/>
    </svg>
    <div class="brand"><span class="brand-dot"></span><span>Brightwell Keys</span></div>
    <p class="slogan">Helping Motivated People<br>Achieve Their Real Estate Goals</p>
    <p class="specialists">First Time Home Buyer’s Specialists<br>Assisting You with All of Your<br>Real Estate Needs from<br>CREDIT to CLOSING<br>and BEYOND!</p>
    <p class="sessions">Attend One of Our<br>Monthly First Time Buyer Informational Sessions<br>and Receive A Personalized Home<br>Purchase Plan!</p>
  </section>

  <section class="side side--back">
    <div class="brand"><span class="brand-dot"></span><span>Brightwell Keys</span></div>
    <ul class="services">
      <li>Rochester’s Best Realtors</li>
      <li>First Time Buyer Grant Assistance</li>
      <li>Mortgage Preparation Counseling</li>
      <li>Customized Property Search</li>
      <li>Closing and Post-Closing Assistance</li>
    </ul>
    <div class="sell">
      <p class="sell-question">Need to Sell Your Property?</p>
      <p class="sell-call">Call us today</p>
      <p class="sell-free">for a free consultation</p>
      <p class="sell-phone">555-KEYS</p>
    </div>
    <p class="contact">www.brightwellkeys.com<br>Residential Investment Commercial</p>
  </section>
</body>
</html>
```